BRIGHT RIVER POWER.

I'd like my business logo.
contact name: Dennis Halvorsen
phone:0438759164
email: info@brightriverpower.net.au
website: www.brightriverpower.net.au

services:
solar
battery storage
LED lighting
energy saving solutions
general electrical
I'd like the design to look professional

Target Market(s)

Everyone

Industry/Entity Type

Business

Contact Information for Business Card

as described above

Requirements
Must have
• Id like the colours and the design to work well with my logo.

```html
<!DOCTYPE html>
<html lang="en">
<head>
<meta charset="utf-8">
<title>Bright River Power – Business Card</title>
<link href="https://fonts.googleapis.com/css2?family=Montserrat:wght@400;500;700&display=swap" rel="stylesheet">
<style>
  :root {
    --stage: #d9d4cb;
    --card: #0c0c0c;
    --card-edge: #1c1c1c;
    --green: #6cc04a;
    --orange: #f2a92e;
    --text: #f2f2f2;
  }
  * { margin: 0; padding: 0; box-sizing: border-box; }
  html, body {
    width: 1200px; height: 1022px; overflow: hidden;
    background: var(--stage);
    font-family: "Montserrat", Arial, sans-serif;
  }
  .stage {
    width: 1200px; height: 1022px;
    display: flex; flex-direction: column; align-items: center; justify-content: center;
    gap: 60px;
  }
  .card {
    width: 700px; height: 400px;
    background: linear-gradient(135deg, var(--card-edge), var(--card) 55%);
    border-radius: 22px;
    position: relative; overflow: hidden;
    box-shadow: 0 10px 30px rgba(0,0,0,.25);
  }

  /* Front */
  .card-front {
    display: flex; flex-direction: column;
    padding: 38px 48px 30px;
  }
  .sun-graphic {
    position: absolute; right: -70px; top: -50px;
    width: 290px; height: 290px; border-radius: 50%;
    background: radial-gradient(circle at 45% 55%, #7fd06a 0%, #3fae5c 45%, rgba(242,169,46,.85) 47%, rgba(242,169,46,0) 70%);
    opacity: .9;
  }
  .brand {
    display: flex; align-items: center; gap: 12px;
    position: relative;
  }
  .brand-dot {
    width: 28px; height: 28px; border-radius: 50%;
    background: var(--green); flex: none;
  }
  .brand-name {
    font-weight: 700; font-size: 24px; color: var(--green);
    letter-spacing: .5px; white-space: nowrap;
  }
  .contact-name {
    margin-top: 30px;
    font-weight: 500; font-size: 24px; line-height: 30px; color: var(--orange);
  }
  .contact-list {
    list-style: none; font-size: 16px; color: var(--text); line-height: 26px;
  }
  .contact-details { margin-top: 8px; }
  .services { margin-top: 6px; }
  .contact-list li { display: flex; align-items: center; gap: 12px; white-space: nowrap; }
  .contact-list svg { width: 15px; height: 15px; flex: none; }
  .services li::before {
    content: ""; width: 8px; height: 8px; border-radius: 50%;
    background: var(--orange); margin: 0 3.5px; flex: none;
  }

  /* Back */
  .back-graphic {
    position: absolute; left: 50%; top: 50%;
    width: 340px; height: 340px; margin: -170px 0 0 -170px; border-radius: 50%;
    background: radial-gradient(circle at 45% 55%, #7fd06a 0%, #3fae5c 45%, rgba(242,169,46,.85) 47%, rgba(242,169,46,0) 70%);
    opacity: .9;
  }
</style>
</head>
<body>
<main class="stage">
  <section class="card card-front">
    <div class="sun-graphic" role="img" aria-label="Sun and leaf illustration in yellow and green"></div>
    <div class="brand">
      <span class="brand-dot"></span>
      <span class="brand-name">BRIGHT RIVER POWER</span>
    </div>
    <h2 class="contact-name">Dennis Halvorsen</h2>
    <ul class="contact-list contact-details">
      <li>
        <svg viewBox="0 0 16 16"><path d="M4 1l3 3-2 2c1 2 3 4 5 5l2-2 3 3-2 3C7 14 2 9 1 3z" fill="var(--orange)"/></svg>
        0438759164
      </li>
      <li>
        <svg viewBox="0 0 16 16"><rect x="1" y="3" width="14" height="10" rx="1" fill="none" stroke="var(--orange)" stroke-width="1.6"/><path d="M1.5 4l6.5 5 6.5-5" fill="none" stroke="var(--orange)" stroke-width="1.6"/></svg>
        info@brightriverpower.net.au
      </li>
      <li>
        <svg viewBox="0 0 16 16"><circle cx="8" cy="8" r="6.5" fill="none" stroke="var(--orange)" stroke-width="1.6"/><path d="M1.5 8h13M8 1.5c-3 3.5-3 9.5 0 13M8 1.5c3 3.5 3 9.5 0 13" fill="none" stroke="var(--orange)" stroke-width="1.2"/></svg>
        www.brightriverpower.net.au
      </li>
    </ul>
    <ul class="contact-list services">
      <li>Solar</li>
      <li>Battery storage</li>
      <li>LED lighting</li>
      <li>Energy saving solutions</li>
    </ul>
  </section>

  <section class="card card-back">
    <div class="back-graphic" role="img" aria-label="Large sun and leaf illustration in yellow and green"></div>
  </section>
</main>
</body>
</html>
```